Process Serving Company needs a letterhead design

Looking to have a letterhead designed for letters to attorneys advertising our business. We would like something eye catching but professional. Colors and logos are attached. Please add "Process Service and Attorney Support" near the logo or header

Target Market(s)

Attorneys

Font styles to use
Serif
Sans Serif

Colors
33a6d7
0255a3
85cae6
cee9f5
ecf7fb

```html
<!DOCTYPE html>
<html lang="en">
<head>
<meta charset="utf-8">
<title>Mesa Ridge Serve Letterhead</title>
<link href="https://fonts.googleapis.com/css2?family=Lato:wght@400;700&family=Kaushan+Script&display=swap" rel="stylesheet">
<style>
  :root {
    --brand-blue: #1d95d3;
    --band-blue: #1a97d6;
    --band-dark: #141414;
    --ink: #3a3a3a;
    --ink-soft: #555555;
    --paper: #ffffff;
    --backdrop: #dcdde3;
  }
  * { margin: 0; padding: 0; box-sizing: border-box; }
  html, body {
    width: 1200px; height: 1200px; overflow: hidden;
    background: var(--backdrop);
  }
  .canvas { position: relative; width: 1200px; height: 1200px; }
  .letterhead {
    position: absolute; left: 334px; top: 226px;
    width: 537px; height: 756px;
    background: var(--paper);
    font-family: "Lato", sans-serif;
    color: var(--ink);
    overflow: hidden;
  }
  .brand {
    position: absolute; left: 37px; top: 33px;
    display: flex; align-items: center; gap: 9px;
  }
  .brand-square { width: 28px; height: 28px; background: var(--brand-blue); flex: none; }
  .brand-text { display: flex; flex-direction: column; }
  .brand-name {
    font-family: "Lato", sans-serif;
    font-weight: 400; font-size: 17px; line-height: 1.05;
    color: var(--brand-blue); letter-spacing: 0.3px;
  }
  .brand-tagline {
    font-size: 8px; line-height: 1; margin-top: 5px;
    color: var(--ink-soft); letter-spacing: 0.4px;
  }
  .address {
    position: absolute; right: 40px; top: 40px;
    display: flex; gap: 4px;
    font-size: 8.5px; line-height: 13px; color: var(--ink-soft);
  }
  .address svg { width: 9px; height: 9px; margin-top: 2px; }
  .letter-body {
    position: absolute; left: 39px; top: 207px; width: 458px;
  }
  .salutation { font-size: 10.5px; margin-bottom: 14px; }
  .paragraph {
    font-size: 10.3px; line-height: 17.4px; color: var(--ink-soft);
    text-align: justify; margin-bottom: 12px;
  }
  .closing { font-size: 12.5px; margin-top: 20px; color: var(--ink-soft); }
  .signature {
    font-family: "Kaushan Script", cursive;
    font-size: 20px; color: var(--brand-blue); margin-top: 4px;
  }
  .footer-wave {
    position: absolute; left: 0; bottom: 0; width: 537px; height: 80px;
  }
  .footer-contacts {
    position: absolute; left: 0; right: 0; bottom: 9px;
    display: flex; justify-content: center; gap: 14px;
    font-size: 8.5px; color: #ffffff;
  }
  .contact-item { display: flex; align-items: center; gap: 4px; }
  .contact-item svg { width: 8px; height: 8px; }
</style>
</head>
<body>
<div class="canvas">
  <div class="letterhead">
    <div class="brand">
      <span class="brand-square"></span>
      <div class="brand-text">
        <span class="brand-name">MESA RIDGE SERVE</span>
        <span class="brand-tagline">Process Service and Attorney Support</span>
      </div>
    </div>

    <div class="address">
      <svg viewBox="0 0 10 10"><circle cx="5" cy="5" r="4.5" fill="none" stroke="#1d95d3"/><circle cx="5" cy="4.2" r="1.4" fill="#1d95d3"/><path d="M3.3 5 L5 8 L6.7 5Z" fill="#1d95d3"/></svg>
      <div>4180 E Canyon Rd STE 210<br>Tempe AZ 85281</div>
    </div>

    <div class="letter-body">
      <p class="salutation">Dear Mr. Lorem,</p>
      <p class="paragraph">Lorem ipsum dolor sit amet, consectetuer adipiscing elit, sed diam nonummy nibh euismod tincidunt ut laoreet dolore magna aliquam erat volutpat. Ut wisi enim ad minim veniam, quis nostrud exerci tation ullamcorper suscipit lobortis nisl ut aliquip ex ea commodo consequat. Duis autem vel eum iriure dolor in hendiusto odio dignissim qui blandit praesent luptatum zzril delenit augue duis dolore te feugait nulla facilisi.</p>
      <p class="paragraph">Lorem ipsum dolor sit amet, consectetuer adipiscing elit, sed diam nonummy nibh euismod tincidunt ut laoreet dolore magna aliquam erat volutpat. Ut wisi enim ad minim veniam, quis nostrud exerci tation ullamcorper suscipit lobortis nisl ut aliquip ex ea commodo consequat. Duis autem vel eum iriure dolor in hendiusto odio dignissim qui blandit praesent luptatum zzril delenit augue duis dolore te feugait nulla facilisi.</p>
      <p class="paragraph">Lorem ipsum dolor sit amet, consectetuer adipiscing elit, sed diam nonummy nibh euismod tincidunt ut laoreet dolore magna aliquam erat volutpat. Ut wisi enim ad minim veniam, quis nostrud exerci tation ullamcorper suscipit lobortis nisl ut aliquip ex ea commodo consequat. Duis autem vel eum iriure dolor in hendiusto odio dignissim qui blandit praesent luptatum zzril delenit augue duis dolore te feugait nulla facilisi.</p>
      <p class="closing">Sincerely Your,</p>
      <p class="signature">Your Name</p>
    </div>

    <svg class="footer-wave" viewBox="0 0 537 80" preserveAspectRatio="none">
      <path d="M0,0 C90,30 220,32 360,30 C450,28 505,32 537,38 L537,80 L0,80 Z" fill="var(--band-dark)"/>
      <path d="M0,18 C100,38 230,39 360,36 C450,34 505,37 537,41 L537,80 L0,80 Z" fill="#ffffff"/>
      <path d="M0,23 C100,42 230,43 360,40 C450,38 505,40 537,44 L537,80 L0,80 Z" fill="var(--band-blue)"/>
    </svg>

    <div class="footer-contacts">
      <span class="contact-item">
        <svg viewBox="0 0 10 10"><path d="M2 1 L4 1 L4.6 3.2 L3.4 4.2 C4 5.5 4.6 6.1 5.8 6.6 L6.8 5.4 L9 6 L9 8 C9 8.6 8.6 9 8 9 C4.5 9 1 5.5 1 2 C1 1.4 1.4 1 2 1Z" fill="#fff"/></svg>
        480 555 0142
      </span>
      <span class="contact-item">
        <svg viewBox="0 0 10 10"><rect x="2.5" y="0.5" width="5" height="9" rx="1" fill="#fff"/><rect x="3.3" y="1.6" width="3.4" height="5.6" fill="#1a97d6"/></svg>
        480 555 0198
      </span>
      <span class="contact-item">
        <svg viewBox="0 0 10 10"><rect x="0.5" y="2" width="9" height="6" fill="#fff"/><path d="M0.5 2 L5 5.5 L9.5 2" fill="none" stroke="#1a97d6" stroke-width="0.8"/></svg>
        Dana@MesaRidgeServe.com
      </span>
      <span class="contact-item">
        <svg viewBox="0 0 10 10"><circle cx="5" cy="5" r="4.3" fill="none" stroke="#fff"/><ellipse cx="5" cy="5" rx="1.8" ry="4.3" fill="none" stroke="#fff" stroke-width="0.8"/><line x1="0.7" y1="5" x2="9.3" y2="5" stroke="#fff" stroke-width="0.8"/></svg>
        MesaRidgeServe.com
      </span>
    </div>
  </div>
</div>
</body>
</html>
```